Heron Property Inspection business card

I am the principal inspector of Heron Property Inspections. I serve Northern Virginia from Winchester to Arlington.Associate, Federated Guild of Dwelling Examiners (FGDE)Graduate, FGDE Home Inspectors CourseNational Association of Home Inspectors ExamI'd like the business card to look more professional than comical.I pulled the attached picture off the web. I'd like to have something like that or an image of a house as my logo on the cards.

Target Market(s)

Persons who recently purchased a home.

Industry/Entity Type

Business

Contact Information for Business Card

Bob AllenBadger Home Inspections, LLC.4455 River RoadBluemont, Virginia 20135cell: 703-231-6680e-mail: tkmarlow@postvale.net

Font styles to use
Serif
Sans Serif

Requirements
Must have
• I'd like to have a logo, something that identifies me as a home inspector. The attached images are something that I'd like to have incorporated into my business card logo.
Nice to have
• I'd like a sketch of a house and/or a magnifying glass showing a house being inspected. The attached images are used as a suggestion only, I do not own the images.
Should not have
• Gimmicky stuff. I want to appear professional and trustworthy.

```html
<!DOCTYPE html>
<html lang="en">
<head>
<meta charset="utf-8">
<title>Heron Property Inspections – Business Card</title>
<link rel="stylesheet" href="https://fonts.googleapis.com/css2?family=Ubuntu:wght@400;500&display=swap">
<style>
  :root {
    --backdrop: #e9e7e3;
    --card-white: #f7f7f7;
    --brand-blue: #2a4fb0;
    --brand-blue-deep: #1d3c96;
    --brand-blue-light: #4a6fcf;
    --arc-grey: #9a9a9a;
    --title-blue: #5577c4;
    --muted-grey: #7a7a7a;
    --text-white: #ffffff;
  }
  html, body {
    margin: 0;
    width: 1200px;
    height: 818px;
    overflow: hidden;
    background: var(--backdrop);
  }
  .business-card {
    position: absolute;
    left: 150px;
    top: 152px;
    width: 900px;
    height: 514px;
    box-shadow: 0 14px 30px rgba(0,0,0,0.22);
    overflow: hidden;
    font-family: "Ubuntu", sans-serif;
  }
  .card-shapes {
    position: absolute;
    inset: 0;
  }
  .brand-name {
    position: absolute;
    left: 70px;
    top: 172px;
    margin: 0;
    font-family: "Ubuntu", sans-serif;
    font-weight: 500;
    font-size: 25px;
    line-height: 1.2;
    color: var(--brand-blue);
    white-space: nowrap;
  }
  .person {
    position: absolute;
    left: 140px;
    top: 300px;
  }
  .person-name {
    font-size: 34px;
    font-weight: 500;
    color: var(--title-blue);
    margin: 0;
  }
  .person-role {
    font-size: 21px;
    color: var(--muted-grey);
    margin: 2px 0 0 4px;
  }
  .contact {
    position: absolute;
    right: 46px;
    top: 150px;
    text-align: right;
    color: var(--text-white);
    font-size: 24px;
    line-height: 1.45;
  }
  .contact-line {
    display: flex;
    justify-content: flex-end;
    align-items: center;
    gap: 14px;
  }
  .contact-icon {
    width: 22px;
    height: 22px;
    flex: none;
  }
  .icon-spacer { width: 22px; flex: none; }
</style>
</head>
<body>
  <div class="business-card">
    <svg class="card-shapes" viewBox="0 0 900 514" width="900" height="514" aria-hidden="true">
      <defs>
        <linearGradient id="blueField" x1="0" y1="0" x2="1" y2="1">
          <stop offset="0" stop-color="#4a6fcf"/>
          <stop offset="1" stop-color="#1d3c96"/>
        </linearGradient>
      </defs>
      <rect width="900" height="514" fill="url(#blueField)"/>
      <path d="M0,0 H392 C610,120 560,470 70,514 H0 Z" fill="#9a9a9a"/>
      <path d="M0,0 H372 C585,125 535,462 52,514 H0 Z" fill="#f7f7f7"/>
    </svg>

    <p class="brand-name">Heron Property Inspections, LLC</p>

    <div class="person">
      <p class="person-name">Employee Name</p>
      <p class="person-role">Managing Director</p>
    </div>

    <div class="contact">
      <div class="contact-line"><span>7182 Quarry Lane</span><span class="icon-spacer"></span></div>
      <div class="contact-line"><span>Fernhill, Virginia 20148</span><span class="icon-spacer"></span></div>
      <div class="contact-line">
        <span>703-555-0192</span>
        <svg class="contact-icon" viewBox="0 0 22 22" aria-label="phone" role="img">
          <rect x="5" y="1" width="12" height="20" rx="2" fill="none" stroke="#ffffff" stroke-width="2"/>
          <rect x="8" y="4" width="6" height="7" fill="#ffffff"/>
          <circle cx="11" cy="17" r="1.5" fill="#ffffff"/>
        </svg>
      </div>
      <div class="contact-line">
        <span>tkmarlow@postvale.net</span>
        <svg class="contact-icon" viewBox="0 0 22 22" aria-label="email" role="img">
          <rect x="1" y="4" width="20" height="14" fill="#ffffff"/>
          <path d="M1,4 L11,12 L21,4" fill="none" stroke="#2a4fb0" stroke-width="1.6"/>
        </svg>
      </div>
    </div>
  </div>
</body>
</html>
```